varlo.com music website

I need a graphic designer to help me design a very modern looking theme for varlo.com, a website for sharing songs. I currently have a very ugly old-looking design that I want to replace. I need a great logo, a great page theme. Just one comp is all I need of the home page. Must have two tag lines: "it pays to share" and "get paid to share music" The current design has all the elements I need, so I have attached it as a download. varlo is pronounced tooney. the current site is not live. Please feel free to send me questions.
Updates

Project Deadline Extended
Reason: I want to give everyone a chance to get their design in. Thank you.

Target Market(s)

The site needs to appeal to music fans that will be pulled in by the concept of "it pays to share," as well as the pop of the design. It has to look fun and cool. Empahsis on modern looking design.

Industry/Entity Type

Graphic Designer

Requirements
Must have
• engaging logo, there must be a container that holds video, scrolls right and left. 6 action buttons, for Chatterleaf, Pipwhistle, My, Add, Search, More. You can put the first letter only on the buttons. Must have two tag lines: "it pays to share" and "get paid to share music" Please include the elements, such as login, join, etc... that are in the comp that you can download. Obviously I don't want it to look like what I already have, except that it must have a container that holds the video. The container that holds the video has to have the same aspect ratio that clipvane uses for it's embed codes. You can find this ratio by checking any clipvane video embed code, they have a custom size tool which lets you play with the sizes. Any question, pls contact thanks.
Nice to have
• unlike the existing comp, it can have white space. Just looking for a good modern theme with a cool logo. Jquery style themes might be nice... Also, think along the lines of a cool techy feel for mobile...

This is a cool image, but obviously don't get too close to it because it belongs to another music site:

http://mbgadgetloop2011.files.blogharbor.example/2012/03/screen-shot-2012-03-28-at-12-02-36-pm.png?w=194

```html
<!DOCTYPE html>
<html lang="en">
<head>
<meta charset="utf-8">
<title>varlo — it pays to share</title>
<link href="https://fonts.googleapis.com/css2?family=Questrial&family=Varela+Round&family=Roboto:wght@400;700&display=swap" rel="stylesheet">
<style>
  :root{
    --navy:#272943;
    --navy-glow:#4a4d82;
    --topline:#5a5c8c;
    --link-blue:#7390e6;
    --logo-blue:#6f8ff0;
    --yellow:#f2c230;
    --orange:#f27a3c;
    --orange-dark:#b9531f;
    --account-bg:#4d4e7a;
    --frame-dark:#1f1f24;
    --frame-grey:#c9c9cc;
    --white:#ffffff;
    --ink:#111111;
    --muted:#9a9a9a;
    --card-hl:#fffcc0;
    --banner:#4e4672;
    --banner-fold:#1c1b2c;
  }
  *{box-sizing:border-box;margin:0;padding:0}
  html,body{width:1200px;height:1134px;overflow:hidden;background:var(--white)}
  .page{position:relative;width:1200px;height:1134px;overflow:hidden;font-family:"Roboto",Arial,sans-serif}

  .hero{position:absolute;left:0;top:0;width:1200px;height:626px;z-index:2;
    background:radial-gradient(ellipse 420px 300px at 600px 300px,var(--navy-glow),var(--navy) 100%);
    border-top:4px solid var(--topline)}
  .stage{position:absolute;left:0;top:626px;width:1200px;height:299px;z-index:1;
    background:linear-gradient(#c9c9cd 0,#f4f4f5 40px,#fff 80px)}
  .footer{position:absolute;left:0;top:925px;width:1200px;height:209px;
    background:radial-gradient(ellipse 420px 200px at 600px 140px,#3f4272,var(--navy) 100%)}

  .account-links{position:absolute;top:1px;right:126px;display:flex;align-items:center;height:32px;list-style:none}
  .account-links li{font-family:"Questrial",sans-serif;font-size:14px;color:var(--white);padding:0 16px;line-height:32px}
  .account-links .account{background:var(--account-bg);padding:0 15px}

  .brand{position:absolute;left:136px;top:16px;font-family:"Varela Round",sans-serif;font-size:84px;color:var(--logo-blue);letter-spacing:-2px;line-height:1}

  .main-nav{position:absolute;top:80px;right:126px;display:flex;gap:48px;list-style:none}
  .main-nav li{font-family:"Questrial",sans-serif;font-size:20px;color:var(--link-blue)}

  .tagline{position:absolute;top:130px;left:0;width:1200px;text-align:center;font-family:"Questrial",sans-serif;font-weight:400;font-size:37px;color:var(--yellow)}

  .stats{position:absolute;left:282px;top:245px;font-size:12px;font-style:italic;color:var(--white)}
  .stats span{margin-right:22px}
  .stats em{color:var(--yellow)}

  .download{position:absolute;left:802px;top:218px;width:118px;height:37px;background:var(--orange);color:var(--white);
    font-weight:700;font-size:16px;display:flex;align-items:center;justify-content:center;gap:8px}
  .download::before{content:"";position:absolute;left:0;top:-10px;border-left:10px solid var(--orange-dark);border-top:10px solid transparent}

  .side-slide{position:absolute;top:366px;width:156px;height:222px;background:#d8d8dc;padding:5px}
  .side-slide.left{left:127px}
  .side-slide.right{left:918px}
  .side-slide .shot{width:100%;height:100%}
  .side-slide.left .shot{background:linear-gradient(135deg,#5a3a36,#b07a60 50%,#e8e0dc)}
  .side-slide.right .shot{background:linear-gradient(135deg,#e8e4e4,#8a5050 50%,#3a3a48)}
  .slide-arrow{position:absolute;top:440px}

  .video-frame{position:absolute;left:282px;top:280px;width:638px;height:406px;background:var(--frame-grey);
    box-shadow:0 12px 16px rgba(0,0,0,.25)}
  .video-frame::before{content:"";position:absolute;left:0;top:0;width:638px;height:300px;background:var(--frame-dark)}
  .video{position:absolute;left:10px;top:10px;width:618px;height:386px;
    background:radial-gradient(ellipse at 65% 40%,#7a5a44,#3a2a22 55%,#181210)}
  .play{position:absolute;left:246px;top:130px}

  .track-title{position:absolute;top:700px;left:0;width:1200px;text-align:center;font-family:"Questrial",sans-serif;font-weight:700;font-size:29px;color:var(--ink);z-index:3}

  .carousel-btn{position:absolute;top:792px;width:48px;height:48px;border-radius:50%;background:#fff;box-shadow:0 2px 5px rgba(0,0,0,.3);display:flex;align-items:center;justify-content:center;z-index:3}
  .carousel-btn.prev{left:138px}
  .carousel-btn.next{left:1016px}

  .video-card{position:absolute;top:776px;width:229px;height:77px;background:#fff;border:1px solid #e2e2e2;box-shadow:0 1px 3px rgba(0,0,0,.12);padding:6px;display:flex;gap:12px;z-index:3}
  .video-card.active{background:var(--card-hl)}
  .thumb{position:relative;width:116px;height:64px;flex:none}
  .thumb .time{position:absolute;right:4px;bottom:2px;font-size:11px;font-weight:700;color:#fff}
  .thumb.t1{background:linear-gradient(#d8d4cc,#3a3634 60%,#1a1a1a)}
  .thumb.t2{background:linear-gradient(#1a2a70,#4aa0e0 50%,#1a1a40)}
  .thumb.t3{background:linear-gradient(135deg,#5a1a5a,#c060b0 50%,#2a0a2a)}
  .card-text h3{font-size:13px;font-weight:400;color:var(--ink);line-height:15px;margin-top:1px}
  .card-text p{font-size:11px;color:var(--muted);line-height:14px}

  .banner{position:absolute;left:329px;top:918px;width:542px;height:68px;background:var(--banner);color:var(--white);z-index:3;
    font-family:"Questrial",sans-serif;font-size:37px;display:flex;align-items:center;justify-content:center;box-shadow:0 8px 10px rgba(0,0,0,.35)}
  .banner::before,.banner::after{content:"";position:absolute;top:0;border-top:7px solid transparent}
  .banner::before{left:-8px;border-right:8px solid var(--banner-fold)}
  .banner::after{right:-8px;border-left:8px solid var(--banner-fold)}

  .social{position:absolute;top:1020px;left:0;width:1200px;display:flex;justify-content:center;gap:14px;list-style:none}
  .social li{display:flex;align-items:center;gap:6px;font-size:12px;color:var(--white)}
  .social i{display:block;width:36px;height:36px;border-radius:7px;border:2px solid #d8d8e0}
  .c1{background:#3b5998}.c2{background:#3aa8dc}.c3{background:#1d5e9a}.c4{background:#f2711c}.c5{background:#c4172c}.c6{background:#b31217}

  .copyright{position:absolute;top:1085px;left:0;width:1200px;text-align:center;font-family:"Questrial",sans-serif;font-size:12px;color:var(--white)}
</style>
</head>
<body>
<div class="page">
  <header class="hero">
    <ul class="account-links">
      <li>TERMS</li><li>PRIVACY</li><li>SUPPORT</li>
      <li class="account">LOGIN</li><li class="account">JOIN</li>
    </ul>
    <div class="brand">varlo</div>
    <ul class="main-nav"><li>HOME</li><li>ABOUT</li><li>SETTINGS</li></ul>
    <h1 class="tagline">IT PAYS TO SHARE</h1>
    <div class="stats"><span>10,456 <em>Varlos</em></span><span>11,223 <em>Fans</em></span></div>
    <div class="download">
      <svg width="16" height="16" viewBox="0 0 16 16"><path d="M6 1h4v6h3l-5 5-5-5h3z" fill="#fff"/><rect x="1" y="13" width="14" height="2" fill="#fff"/></svg>
      Download
    </div>

    <div class="side-slide left"><div class="shot" role="img" aria-label="Photo of a singer performing with a crowd"></div></div>
    <div class="side-slide right"><div class="shot" role="img" aria-label="Photo of friends posing at a party"></div></div>
    <svg class="slide-arrow" style="left:170px" width="46" height="80" viewBox="0 0 46 80"><path d="M36 0h10L12 40l34 40H36L0 40z" fill="#fff"/></svg>
    <svg class="slide-arrow" style="left:968px" width="46" height="80" viewBox="0 0 46 80"><path d="M10 0H0l34 40L0 80h10l36-40z" fill="#fff"/></svg>

    <div class="video-frame">
      <div class="video" role="img" aria-label="Featured music video: singer recording at a studio microphone">
        <svg class="play" width="126" height="126" viewBox="0 0 126 126"><circle cx="63" cy="63" r="62" fill="rgba(60,60,60,.75)"/><path d="M52 36v54l30-27z" fill="#8a8a8a"/></svg>
      </div>
    </div>
  </header>

  <section class="stage"></section>
  <h2 class="track-title">Vampire Lovae</h2>

  <div class="carousel-btn prev"><svg width="14" height="20" viewBox="0 0 14 20"><path d="M11 2L3 10l8 8" stroke="#999" stroke-width="3" fill="none"/></svg></div>
  <article class="video-card active" style="left:214px">
    <div class="thumb t1" role="img" aria-label="Band photo thumbnail"><span class="time">2:05</span></div>
    <div class="card-text"><h3>Neque porro quisquam</h3><p>b4 lbus067</p><p>79,345 views</p></div>
  </article>
  <article class="video-card" style="left:486px">
    <div class="thumb t2" role="img" aria-label="Concert light show thumbnail"><span class="time">10:46</span></div>
    <div class="card-text"><h3>Neque porro quisquam</h3><p>b4 lbus067</p><p>79,345 views</p></div>
  </article>
  <article class="video-card" style="left:757px">
    <div class="thumb t3" role="img" aria-label="Dancer on stage thumbnail"><span class="time">6:30</span></div>
    <div class="card-text"><h3>Neque porro quisquam</h3><p>b4 lbus067</p><p>79,345 views</p></div>
  </article>
  <div class="carousel-btn next"><svg width="14" height="20" viewBox="0 0 14 20"><path d="M3 2l8 8-8 8" stroke="#999" stroke-width="3" fill="none"/></svg></div>

  <footer class="footer"></footer>
  <div class="banner">GET PAID TO SHARE MUSIC</div>
  <ul class="social">
    <li><i class="c1"></i>Chatterleaf</li>
    <li><i class="c2"></i>Pipwhistle</li>
    <li><i class="c3"></i>Nudgely</li>
    <li><i class="c4"></i>Quillpost</li>
    <li><i class="c5"></i>Tunelog</li>
    <li><i class="c6"></i>clipvane</li>
  </ul>
  <p class="copyright">© 2012 Heartcast Media. All Rights Reserved.</p>
</div>
</body>
</html>
```